Flyer-Design für  Kampfsportschule
Flyer-Design für Kampfsportschule
Zielgruppe
Wir bieten Taekwondo/Selbstverteidigung an. Meine Zielgruppe sind Erwachsene ab 17 Jahren.
Aufgabenstellung
Das Angebot '1 Monat kostenloses Training, oder einen Monat kostenloses Training' und 'Taekwondo/Selbstverteidigung in Weinstadt' soll eingebracht und direkt sichtbar sein. Eventuell auch Punkte wie Selbstbewusstsein, Beweglichkeit, Zielstrebigkeit, Kraft und Ausdauer, körperliche Fitness... Farben: Weiß, schwarz und Schrift in gelb. Nichts rotes.
Die Daten:
Tel: 0176-4819275 Email: m.r.budozentrum@postfach-beispiel.de und www.mrbudozentrum-beispiel.de

```html
<!DOCTYPE html>
<html lang="de">
<head>
<meta charset="utf-8">
<title>Flyer – M.R. Budozentrum</title>
<link href="https://fonts.googleapis.com/css2?family=Open+Sans:wght@400;600;700;800&family=Raleway:wght@700;800&display=swap" rel="stylesheet">
<style>
  :root {
    --ink: #1c1719;
    --accent: #f5c518;
    --on-accent: #1c1719;
    --white: #ffffff;
    --page: #f6f6f6;
  }
  * { box-sizing: border-box; margin: 0; padding: 0; }
  html, body { width: 1200px; height: 817px; overflow: hidden; background: var(--page); }
  body { position: relative; font-family: "Open Sans", sans-serif; color: var(--white); }

  .flyer {
    position: absolute; top: 28px; width: 360px; height: 760px;
    background: var(--ink); overflow: hidden;
  }
  .flyer--front { left: 210px; }
  .flyer--back { left: 630px; }

  /* brand name stand-in */
  .brand { position: absolute; display: flex; align-items: center; gap: 10px; }
  .brand__dot { width: 34px; height: 34px; border-radius: 50%; background: var(--white); flex: none; }
  .brand__name { font-weight: 700; font-size: 16px; line-height: 1.2; color: var(--white); }

  /* front */
  .front__photo {
    position: absolute; right: 0; top: 0; width: 230px; height: 470px;
    background: linear-gradient(160deg, #3a3335 0%, #6c6466 45%, #d8d5d5 75%, #2a2325 100%);
  }
  .front__brand { left: 24px; top: 42px; width: 160px; }
  .headline { position: absolute; left: 22px; top: 396px; }
  .headline__line {
    display: inline-block; background: var(--accent); color: var(--on-accent);
    font-family: "Raleway", sans-serif; font-weight: 800; font-size: 28px;
    padding: 2px 12px 6px; line-height: 1.1;
  }
  .headline__line + .headline__line { margin-top: 6px; }
  .front__intro { position: absolute; left: 24px; top: 494px; width: 316px; }
  .front__lead { font-weight: 800; font-size: 15px; margin-bottom: 6px; }
  .front__copy { font-size: 12.5px; line-height: 1.6; font-style: italic; }
  .offer {
    position: absolute; left: 40px; top: 600px; width: 280px; height: 110px;
    border: 3px solid var(--accent); text-align: center; padding-top: 10px;
  }
  .offer__month { color: var(--accent); font-weight: 800; font-size: 24px; line-height: 1.1; }
  .offer__text { font-weight: 800; font-size: 24px; line-height: 1.15; }
  .band {
    position: absolute; left: 0; bottom: 0; width: 100%; height: 36px;
    background: var(--accent); color: var(--on-accent);
    display: flex; align-items: center; justify-content: center;
    font-weight: 700; font-size: 12.5px;
  }

  /* back */
  .back__photo {
    position: absolute; left: 0; top: 0; width: 100%; height: 200px;
    background: linear-gradient(180deg, #2c2728 0%, #5b5254 40%, #8a6a55 80%, #4a3a30 100%);
  }
  .back__banner {
    position: absolute; left: 0; top: 200px; width: 100%; height: 56px;
    background: var(--accent); color: var(--on-accent);
    padding: 9px 18px; font-weight: 700; font-size: 13.5px; line-height: 1.35;
  }
  .back__question { position: absolute; left: 18px; top: 272px; width: 325px; font-size: 14px; line-height: 1.45; }
  .back__question em { color: var(--accent); font-style: normal; font-weight: 600; }
  .benefits { position: absolute; left: 18px; top: 332px; list-style: none; }
  .benefits li { font-weight: 700; font-size: 12.5px; line-height: 1; margin-bottom: 12px; display: flex; align-items: center; gap: 12px; }
  .benefits li::before { content: ""; width: 7px; height: 7px; border-radius: 50%; background: var(--accent); }
  .back__brand { right: 16px; top: 382px; width: 140px; }
  .back__invite { position: absolute; left: 18px; top: 512px; width: 325px; font-size: 12.5px; line-height: 1.6; }
  .contact { position: absolute; left: 0; top: 578px; width: 100%; text-align: center; }
  .contact__cta { font-weight: 700; font-size: 18px; }
  .contact__phone { font-weight: 800; font-size: 24px; margin-top: 8px; color: var(--accent); }
  .contact__mail { font-size: 12px; margin-top: 8px; }
</style>
</head>
<body>

<section class="flyer flyer--front">
  <div class="front__photo" role="img" aria-label="Foto einer Taekwondo-Sportlerin im weißen Dobok mit schwarzem Kragen in Abwehrhaltung"></div>
  <div class="brand front__brand">
    <span class="brand__dot"></span>
    <span class="brand__name">M.R.<br>Budozentrum</span>
  </div>
  <h1 class="headline">
    <span class="headline__line">Selbstverteidigung</span><br>
    <span class="headline__line">in Weinstadt</span>
  </h1>
  <div class="front__intro">
    <p class="front__lead">Anfänger sind herzlich willkommen!</p>
    <p class="front__copy">Teste uns jetzt ganz unverbindlich in einem Probetraining und lerne unsere Gruppe, sowie unsere Trainer kennen und lass uns DEINE Ziele erreichen.</p>
  </div>
  <div class="offer">
    <p class="offer__month">1 Monat</p>
    <p class="offer__text">kostenloses<br>Training</p>
  </div>
  <div class="band">www.mrbudozentrum-beispiel.de</div>
</section>

<section class="flyer flyer--back">
  <div class="back__photo" role="img" aria-label="Gruppenfoto der Trainingsgruppe im Dojo mit Urkunden"></div>
  <p class="back__banner">Ihr Ansprechpartner für Kampfsport und Fitness in Weinstadt</p>
  <p class="back__question">Was bekommen Sie, wenn Sie <em>Selbstverteidigung</em> lernen?</p>
  <ul class="benefits">
    <li>Selbstbewusstsein</li>
    <li>Beweglichkeit</li>
    <li>Selbstverteidigung</li>
    <li>Kraft und Ausdauer</li>
    <li>körperliche Fitness</li>
  </ul>
  <div class="brand back__brand">
    <span class="brand__dot"></span>
    <span class="brand__name">M.R.<br>Budozentrum</span>
  </div>
  <p class="back__invite">Sind Sie interessiert? Dann kommen Sie zu uns in das BUDOZENTRUM REMSTAL.</p>
  <div class="contact">
    <p class="contact__cta">Jetzt anrufen!</p>
    <p class="contact__phone">0176-4819275</p>
    <p class="contact__mail">m.r.budozentrum@postfach-beispiel.de</p>
  </div>
  <div class="band">www.mrbudozentrum-beispiel.de</div>
</section>

</body>
</html>
```